Coastline Premier Retreats Business Card Design

Design a business card for Coastline Premier Retreats. Look at the website for colors and reference. Card should have logo, name, title, office number, mobile number, email, URL and a tagline like, "Luxury Hotel & Resort Email Marketing" (This might change).

https://www.coastlinepremierretreats.example

The rest I will leave up to your imagination.

Contact Information for Business Card

Logo, name, title, office number, mobile number, email, URL and a tagline like, "Luxury Hotel & Resort Email Marketing" (This might change).

```html
<!DOCTYPE html>
<html lang="en">
<head>
<meta charset="utf-8">
<title>Coastline Premier Retreats – Business Card</title>
<link href="https://fonts.googleapis.com/css2?family=Montserrat:wght@700&family=Arimo:wght@400;700&display=swap" rel="stylesheet">
<style>
  :root {
    --stage: #2b2826;
    --card-dark: #1b1b1b;
    --card-light: #ffffff;
    --accent: #f07a22;
    --ink: #111111;
    --paper-text: #ffffff;
  }
  * { box-sizing: border-box; margin: 0; padding: 0; }
  html, body { width: 1200px; height: 900px; overflow: hidden; }
  body {
    background: var(--stage);
    font-family: "Arimo", Arial, sans-serif;
    position: relative;
  }
  .card {
    position: absolute;
    left: 320px;
    width: 560px;
    height: 320px;
    border-radius: 22px;
    overflow: hidden;
    box-shadow: 0 10px 30px rgba(0,0,0,.45);
  }
  .card--back { top: 90px; background: var(--card-dark); }
  .card--front { top: 490px; background: var(--card-light); }

  .wordmark {
    font-family: "Montserrat", Arial, sans-serif;
    font-weight: 700;
    text-transform: uppercase;
    display: flex;
    align-items: center;
    gap: 12px;
    line-height: 1.05;
  }
  .wordmark__square {
    width: 14px; height: 14px;
    background: var(--accent);
    flex: none;
  }
  .card--back .wordmark {
    position: absolute;
    inset: 0;
    justify-content: center;
    color: var(--paper-text);
    font-size: 30px;
    letter-spacing: 1px;
  }

  .card--front .wordmark {
    position: absolute;
    left: 34px; top: 110px;
    width: 200px;
    color: var(--ink);
    font-size: 18px;
  }
  .divider {
    position: absolute;
    left: 262px; top: 36px;
    width: 2px; height: 170px;
    background: var(--accent);
  }
  .details {
    position: absolute;
    left: 282px; top: 28px;
    color: var(--ink);
    font-size: 12px;
    line-height: 1.35;
  }
  .details__name {
    font-family: "Montserrat", Arial, sans-serif;
    font-weight: 700;
    color: var(--accent);
    font-size: 19px;
    text-transform: uppercase;
    margin-bottom: 2px;
  }
  .details__role { margin-bottom: 2px; }
  .contact { list-style: none; margin-top: 4px; }
  .contact li { display: flex; align-items: center; gap: 7px; }
  .contact svg { width: 11px; height: 11px; fill: var(--accent); flex: none; }
  .wave { position: absolute; left: 0; top: 0; width: 560px; height: 320px; }
</style>
</head>
<body>
  <section class="card card--back" aria-label="Card back">
    <div class="wordmark"><span class="wordmark__square"></span><span>Coastline Premier<br>Retreats</span></div>
  </section>

  <section class="card card--front" aria-label="Card front">
    <svg class="wave" viewBox="0 0 560 320" aria-hidden="true">
      <path d="M120 320 C280 305 330 265 400 235 C460 210 510 205 560 205 L560 320 Z" fill="var(--card-dark)"/>
      <path d="M90 300 C250 285 310 240 390 215 C450 196 500 190 545 188 C500 194 455 202 395 225 C320 255 260 298 90 312 Z" fill="var(--accent)"/>
    </svg>

    <div class="wordmark"><span class="wordmark__square"></span><span>Coastline Premier<br>Retreats</span></div>
    <div class="divider"></div>

    <div class="details">
      <p class="details__name">Daniel Marsh</p>
      <p class="details__role">Co-Founder</p>
      <p class="details__tagline">Luxury Hotel &amp; Resort<br>Email Marketing</p>
      <ul class="contact">
        <li><svg viewBox="0 0 24 24"><path d="M6.6 10.8a15 15 0 0 0 6.6 6.6l2.2-2.2a1 1 0 0 1 1-.25 11 11 0 0 0 3.6.6 1 1 0 0 1 1 1V20a1 1 0 0 1-1 1A17 17 0 0 1 3 4a1 1 0 0 1 1-1h3.5a1 1 0 0 1 1 1c0 1.25.2 2.45.6 3.6a1 1 0 0 1-.25 1z"/></svg>555-201-4836</li>
        <li><svg viewBox="0 0 24 24"><path d="M7 1h10a2 2 0 0 1 2 2v18a2 2 0 0 1-2 2H7a2 2 0 0 1-2-2V3a2 2 0 0 1 2-2zm0 3v14h10V4zm5 15.5a1 1 0 1 0 0 2 1 1 0 0 0 0-2z"/></svg>555-318-7042</li>
        <li><svg viewBox="0 0 24 24"><path d="M2 5h20v14H2zm2 2v.5l8 5 8-5V7zm0 3v7h16v-7l-8 5z"/></svg>info@coastlinepremierretreats.example</li>
        <li><svg viewBox="0 0 24 24"><path d="M12 2a10 10 0 1 0 0 20 10 10 0 0 0 0-20zm0 2c.9 1.2 1.6 2.6 2 4h-4c.4-1.4 1.1-2.8 2-4zM4.3 14a8 8 0 0 1 0-4h3.3a16 16 0 0 0 0 4zm.9 2h2.9c.3 1.3.8 2.5 1.4 3.6A8 8 0 0 1 5.2 16zm2.9-8H5.2a8 8 0 0 1 4.3-3.6C8.9 5.5 8.4 6.7 8.1 8zM12 20c-.9-1.2-1.6-2.6-2-4h4c-.4 1.4-1.1 2.8-2 4zm2.3-6H9.7a14 14 0 0 1 0-4h4.6a14 14 0 0 1 0 4zm.2 5.6c.6-1.1 1.1-2.3 1.4-3.6h2.9a8 8 0 0 1-4.3 3.6zm1.9-5.6a16 16 0 0 0 0-4h3.3a8 8 0 0 1 0 4z"/></svg>www.coastlinepremierretreats.example</li>
      </ul>
    </div>
  </section>
</body>
</html>
```